Brookvale Building Company - advertisement poster

I am looking to print some canvas signs to advertise my general contracting company, Brookvale Building Company. The sign will measure 6' long x 3' high so the size should match that ratio. I already have a logo icon, which is the Letter 'B' and some trees that I would like to incorporate, see attached. I would also like the to have the following information listed:
1) phone number: 831-555-0172
2) email: brookvalebuildingcompany@mailnest.example
3) website: brookvalebuildingcompany.example
4) Lic#4826130
5) I want to use this text: "BUILD WITH THE B-CREW!"

The ad should be relatively simple and clean. Black and Green are my company colors. I am open to creative ideas!

Target Market(s)

People looking to renovate their homes

Industry/Entity Type

Construction

Colors
59FF00
82FF00
B8FF75
E3FFCB
F4FFEA

Requirements
Must have
• Must have my company logo
Should not have
• No photos or complex graphics

```html
<!DOCTYPE html>
<html lang="en">
<head>
<meta charset="utf-8">
<title>Brookvale Building Company – Sign</title>
<link rel="stylesheet" href="https://fonts.googleapis.com/css2?family=Michroma&family=Montserrat:wght@900&family=Roboto+Condensed:wght@400;700&family=Poppins:wght@700&display=swap">
<style>
  :root {
    --green: #66a644;
    --ink: #1b1b1b;
    --paper: #ffffff;
    --crane: #e0b13a;
  }
  * { margin: 0; padding: 0; box-sizing: border-box; }
  html, body { width: 1200px; height: 635px; overflow: hidden; background: var(--paper); }
  .sign { position: relative; width: 1200px; height: 635px; background: var(--paper); overflow: hidden; }
  .sign__lower { position: absolute; left: 0; top: 327px; width: 1200px; height: 308px; background: var(--ink); }
  .headline { position: absolute; left: 0; top: 0; width: 1200px; height: 327px; }
  .headline__lead { font-family: "Michroma", sans-serif; fill: var(--ink); }
  .headline__main { font-family: "Montserrat", sans-serif; font-weight: 900; fill: var(--green); }
  .scene-art { position: absolute; left: 0; top: 0; width: 1200px; height: 635px; pointer-events: none; }
  .brand { position: absolute; left: 70px; top: 410px; width: 400px; text-align: center; color: var(--paper);
           font-family: "Michroma", sans-serif; }
  .brand__name { font-size: 40px; line-height: 1.1; letter-spacing: 1px; }
  .brand__sub { font-size: 17px; letter-spacing: 5px; margin-top: 10px; }
  .contact { position: absolute; left: 527px; top: 350px; font-family: "Roboto Condensed", sans-serif; color: var(--paper); }
  .contact__row { display: flex; align-items: center; gap: 12px; }
  .contact__icon { width: 36px; height: 36px; flex: none; }
  .contact__phone { font-size: 46px; font-weight: 700; height: 56px; }
  .contact__email { font-size: 29px; margin-top: 0; height: 54px; }
  .contact__web { font-size: 33px; height: 52px; }
  .license { position: absolute; left: 536px; top: 521px; width: 504px; height: 48px; }
  .license__tag { font-family: "Poppins", sans-serif; font-weight: 700; font-size: 27px; letter-spacing: 6px; fill: var(--paper); }
  .license__num { font-family: "Poppins", sans-serif; font-weight: 700; font-size: 29px; letter-spacing: 4px; fill: var(--ink); }
</style>
</head>
<body>
<main class="sign">
  <div class="sign__lower"></div>

  <svg class="headline" viewBox="0 0 1200 327" aria-label="Build with the B-Crew!">
    <text class="headline__lead" x="55" y="122" font-size="70" textLength="778" lengthAdjust="spacingAndGlyphs">BUILD WITH THE</text>
    <text class="headline__main" x="54" y="293" font-size="196" textLength="782" lengthAdjust="spacingAndGlyphs">B-CREW!</text>
  </svg>

  <svg class="scene-art" viewBox="0 0 1200 635" role="img" aria-label="Illustration of a yellow tower crane lifting steel beams beside green and black pine trees">
    <defs>
      <linearGradient id="craneTone" x1="0" y1="0" x2="1" y2="1">
        <stop offset="0" stop-color="#e9c25a"/>
        <stop offset="1" stop-color="#6aa84a"/>
      </linearGradient>
    </defs>
    <rect x="975" y="90" width="225" height="237" fill="url(#craneTone)" opacity="0.55"/>
    <rect x="1140" y="327" width="60" height="288" fill="var(--crane)" opacity="0.6"/>
  </svg>

  <div class="brand" aria-label="Brookvale Building Company">
    <div class="brand__name">BROOKVALE</div>
    <div class="brand__sub">BUILDING COMPANY</div>
  </div>

  <div class="contact">
    <div class="contact__row contact__phone">
      <svg class="contact__icon" viewBox="0 0 36 36" aria-hidden="true">
        <circle cx="18" cy="18" r="18" fill="var(--green)"/>
        <path d="M12 9c1-.6 2-.4 2.6.6l2 3.2c.5.8.3 1.8-.4 2.4l-1.3 1c.9 2 2.4 3.6 4.4 4.6l1-1.3c.6-.8 1.7-1 2.5-.4l3.1 2.1c.9.6 1.1 1.7.5 2.6l-1 1.4c-.9 1.3-2.6 1.8-4.1 1.2C15.6 24.6 11.5 20.4 9.7 14.7c-.5-1.5.1-3.1 1.3-4z" fill="var(--paper)"/>
      </svg>
      <span>831-555-0172</span>
    </div>
    <div class="contact__row contact__email">
      <svg class="contact__icon" viewBox="0 0 36 36" aria-hidden="true">
        <circle cx="18" cy="18" r="18" fill="var(--green)"/>
        <rect x="9" y="12" width="18" height="13" rx="1" fill="var(--paper)"/>
        <path d="M9.5 12.5 18 19.5l8.5-7" fill="none" stroke="var(--green)" stroke-width="1.6"/>
      </svg>
      <span>brookvalebuildingcompany@mailnest.example</span>
    </div>
    <div class="contact__row contact__web">
      <svg class="contact__icon" viewBox="0 0 36 36" aria-hidden="true">
        <circle cx="18" cy="18" r="18" fill="var(--green)"/>
        <g fill="none" stroke="var(--paper)" stroke-width="1.8">
          <circle cx="18" cy="18" r="9"/>
          <ellipse cx="18" cy="18" rx="4" ry="9"/>
          <path d="M9 18h18M10.5 13.5h15M10.5 22.5h15"/>
        </g>
      </svg>
      <span>www.brookvalebuildingcompany.example</span>
    </div>
  </div>

  <svg class="license" viewBox="0 0 504 48" aria-label="License #4826130">
    <polygon points="0,0 504,0 504,0 504,0" fill="none"/>
    <polygon points="238,0 485,0 504,48 262,48" fill="var(--paper)"/>
    <polygon points="0,0 238,0 262,48 20,48" fill="var(--green)"/>
    <text class="license__tag" x="48" y="34">LICENSE</text>
    <text class="license__num" x="276" y="35">#4826130</text>
  </svg>
</main>
</body>
</html>
```